Business Card Design Project (on hold until logo completed)

Small Pharma Consulting Firm called Coastbeam Consulting. Small business will be focused on ad hoc consulting projects. Business located near the beach so want to play off the location with the "ideas" so a "house of lights or ideas". The concept is to use a variety of experiences and expertise in the Pharma business to help clients use what they already know to tell a story and create ideas that better build customer solutions. Simplicity is key. We hire lots of consultants, create lots of data, conduct lots of research but we often get lost in all of it or do not have time to digest and analyze. We also get inwardly-focused. This small group will compress the information into simple chunks from a customer persective through a unique blend of skills and tools.
Updates

Project Deadline Extended
Reason: Logo is now completed so can begin business card design

Target Market(s)

Pharma Professionals, mostly marketing and analytics but could also be senior leadership

Industry/Entity Type

Business

Font styles to use
Sans Serif

Colors
00a990
fcca95
faa54b

Requirements
Must have
• logo with text
Nice to have
• Space for PO Box on 1 line, then city, state, zip on next line
Background should be white or tan/beige (to be eco-friendly, like the color of a brown paper bag)

```html
<!DOCTYPE html>
<html lang="en">
<head>
<meta charset="utf-8">
<title>Coastbeam Consulting – Business Cards</title>
<link rel="stylesheet" href="https://fonts.googleapis.com/css2?family=Open+Sans:wght@400;600;700&display=swap">
<style>
  :root {
    --teal: #00a990;
    --teal-dark: #0b8f7c;
    --teal-light: #2cc4aa;
    --peach: #fcca95;
    --orange: #faa54b;
    --ink: #3c3c3c;
    --muted: #777777;
    --paper: #ffffff;
    --stage: #e9e4dc;
  }
  * { box-sizing: border-box; margin: 0; padding: 0; }
  html, body {
    width: 1200px; height: 1023px; overflow: hidden;
    background: var(--stage);
    font-family: "Open Sans", Arial, sans-serif;
  }
  .canvas { position: relative; width: 1200px; height: 1023px; }

  .card {
    position: absolute;
    width: 540px; height: 309px;
    border-radius: 4px;
    box-shadow: 0 10px 28px rgba(0,0,0,0.18);
    overflow: hidden;
  }

  /* Front */
  .card-front { left: 70px; top: 130px; background: var(--paper); }
  .card-front .accent-band {
    position: absolute; left: 0; top: 92px; width: 100%; height: 14px;
    background: var(--peach);
  }
  .wordmark {
    position: absolute; left: 34px; top: 34px;
    color: var(--teal); font-weight: 700; line-height: 1;
    font-size: 38px; letter-spacing: 1px; text-transform: uppercase;
    white-space: nowrap;
  }

  .person { position: absolute; right: 34px; top: 128px; text-align: right; }
  .person .full-name {
    color: var(--teal); font-weight: 700; font-size: 18px; letter-spacing: 1px;
    text-transform: uppercase;
  }
  .person .role { color: var(--muted); font-size: 12px; margin-top: 2px; }

  .contact-list {
    position: absolute; right: 34px; top: 184px;
    list-style: none; text-align: right;
    color: var(--ink); font-size: 12.5px; line-height: 20px;
  }
  .contact-list li { display: flex; justify-content: flex-end; align-items: center; gap: 8px; }
  .contact-list svg { width: 13px; height: 13px; fill: var(--teal); }

  .postal {
    position: absolute; right: 34px; bottom: 20px; text-align: right;
    font-style: normal;
    color: var(--teal); font-weight: 700; font-size: 12px; line-height: 18px;
    letter-spacing: 0.6px; text-transform: uppercase;
  }

  /* Back */
  .card-back {
    left: 590px; top: 540px;
    background: linear-gradient(135deg, var(--teal-dark) 0%, var(--teal-light) 55%, var(--teal) 100%);
  }
  .card-back .wordmark {
    left: 0; right: 0; top: 108px; text-align: center;
    color: var(--paper); font-size: 44px;
  }
  .card-back .accent-rule {
    position: absolute; left: 110px; right: 110px; top: 184px; height: 4px;
    background: linear-gradient(90deg, var(--orange), rgba(252,202,149,0));
  }
  .website {
    position: absolute; left: 0; right: 0; bottom: 30px; text-align: center;
    color: var(--paper); font-size: 13px; letter-spacing: 1.5px;
  }
</style>
</head>
<body>
<main class="canvas">

  <section class="card card-front" aria-label="Business card front">
    <div class="accent-band"></div>
    <p class="wordmark">Coastbeam</p>

    <div class="person">
      <p class="full-name">Dana R. Holloway</p>
      <p class="role">Director</p>
    </div>

    <ul class="contact-list">
      <li>(555)010-2231
        <svg viewBox="0 0 24 24" aria-hidden="true"><path d="M6.6 10.8a15.1 15.1 0 0 0 6.6 6.6l2.2-2.2c.3-.3.7-.4 1-.2 1.1.4 2.3.6 3.6.6.6 0 1 .4 1 1V20c0 .6-.4 1-1 1A17 17 0 0 1 3 4c0-.6.4-1 1-1h3.5c.6 0 1 .4 1 1 0 1.3.2 2.5.6 3.6.1.3 0 .7-.2 1z"/></svg></li>
      <li>(555)010-4478
        <svg viewBox="0 0 24 24" aria-hidden="true"><path d="M7 2h10a2 2 0 0 1 2 2v16a2 2 0 0 1-2 2H7a2 2 0 0 1-2-2V4a2 2 0 0 1 2-2zm0 3v12h10V5zm5 13.5a1 1 0 1 0 0 2 1 1 0 0 0 0-2z"/></svg></li>
      <li>dana@coastbeamconsult.com
        <svg viewBox="0 0 24 24" aria-hidden="true"><path d="M3 5h18a1 1 0 0 1 1 1v12a1 1 0 0 1-1 1H3a1 1 0 0 1-1-1V6a1 1 0 0 1 1-1zm9 7.5L4 7.4V17h16V7.4z"/></svg></li>
    </ul>

    <address class="postal">
      P.O. Box 2200 Harbor Street, Any City<br>
      4520 N. Shoreline Ave #210, Seaview, AZ 85000
    </address>
  </section>

  <section class="card card-back" aria-label="Business card back">
    <p class="wordmark">Coastbeam</p>
    <div class="accent-rule"></div>
    <p class="website">www.coastbeamconsult.com</p>
  </section>

</main>
</body>
</html>
```